Customer Value Leaflet

We need a bi-fold brochure designing, based on the attached PDF wireframes. Our company name is brambleharvik.com (of which the logo is currently being designed). The corporate colour is orange (the exact shade of which we are happy to leave to the designers discretion).

The leaflet will distributed to customer experience experts and marketers so the design needs to be bright, engaging, clean and simple. Design is critical.

It Company

```html
<!DOCTYPE html>
<html lang="en">
<head>
<meta charset="utf-8">
<title>Customer Value Leaflet – brambleharvik.com</title>
<link rel="stylesheet" href="https://fonts.googleapis.com/css2?family=Source+Sans+3:wght@400;600&display=swap">
<style>
  :root {
    --brand-orange: #f7941d;
    --band-orange-light: #f9a23a;
    --band-orange-dark: #f28c14;
    --ink: #1f1f1f;
    --paper: #ffffff;
    --figure-light: #d9d9d9;
    --figure-dark: #9a9a9a;
  }
  html, body {
    margin: 0;
    padding: 0;
    width: 1200px;
    height: 1200px;
    overflow: hidden;
    background: var(--paper);
  }
  .leaflet-panel {
    position: relative;
    width: 1200px;
    height: 1200px;
    font-family: "Source Sans 3", "Myriad Pro", Arial, sans-serif;
    color: var(--ink);
  }
  .persona-heading {
    position: absolute;
    top: 60px;
    width: 474px;
    height: 87px;
    margin: 0;
    background: var(--brand-orange);
    color: var(--paper);
    font-weight: 400;
    font-size: 36px;
    letter-spacing: 0.5px;
    line-height: 87px;
    text-align: center;
  }
  .persona-heading.kim { left: 111px; }
  .persona-heading.kevin { left: 601px; }

  .persona-figure {
    position: absolute;
    width: 182px;
    border-radius: 90px 90px 24px 24px;
    background: linear-gradient(180deg, var(--figure-light) 0%, var(--figure-dark) 100%);
  }
  .persona-figure.kim { left: 257px; top: 178px; height: 310px; }
  .persona-figure.kevin { left: 748px; top: 192px; height: 312px; }

  .persona-story {
    position: absolute;
    top: 530px;
    width: 440px;
    margin: 0;
    font-size: 34px;
    line-height: 48px;
    text-align: center;
  }
  .persona-story.kim { left: 128px; }
  .persona-story.kevin { left: 618px; }

  .teaser-band {
    position: absolute;
    left: 0;
    top: 1002px;
    width: 1200px;
    height: 144px;
    background: linear-gradient(180deg, var(--band-orange-light) 0%, var(--band-orange-dark) 100%);
    display: flex;
    align-items: center;
    justify-content: center;
  }
  .teaser-band p {
    margin: 0;
    font-size: 37px;
    color: var(--ink);
  }
</style>
</head>
<body>
  <main class="leaflet-panel">
    <h2 class="persona-heading kim">MEET KIM</h2>
    <h2 class="persona-heading kevin">MEET KEVIN</h2>

    <div class="persona-figure kim" role="img" aria-label="Cartoon illustration of Kim, a customer with hair in a bun wearing a cardigan"></div>
    <div class="persona-figure kevin" role="img" aria-label="Cartoon illustration of Kevin, a customer wearing a jumper and trousers"></div>

    <p class="persona-story kim">Kim has purchased<br>3 items from you over<br>the past 3 months @<br>£109 margin and you<br>acquired her though a<br>Searchly PPC campaign</p>
    <p class="persona-story kevin">Kevin purchased<br>an item last week @<br>£31 margin and you<br>acquired him though a<br>retargeting campaign</p>

    <div class="teaser-band">
      <p>Right now you probably think Kim is your best customer…</p>
    </div>
  </main>
</body>
</html>
```